Business card design for my company.
I would like the card's background colour to be black. You can also see our web site to get an idea of our brand. https://www.tmwhomecrafting.com.au/
- Name
- Email

```html
<!DOCTYPE html>
<html lang="en">
<head>
<meta charset="utf-8">
<title>TMW Home Crafting – Business Cards</title>
<link rel="stylesheet" href="https://fonts.googleapis.com/css2?family=Poppins:wght@400;500;600&display=swap">
<style>
  :root {
    --backdrop: #d6d6d6;
    --card: #000000;
    --ink: #ffffff;
    --brand-green: #1f9a45;
  }
  * { box-sizing: border-box; margin: 0; padding: 0; }
  html, body { width: 1200px; height: 961px; overflow: hidden; }
  body {
    position: relative;
    background: var(--backdrop);
    font-family: "Poppins", sans-serif;
    color: var(--ink);
  }
  .card {
    position: absolute;
    width: 540px;
    height: 315px;
    background: var(--card);
    box-shadow: 0 10px 24px rgba(0,0,0,0.25);
    overflow: hidden;
  }
  .card--front { left: 600px; top: 120px; }
  .card--back  { left: 60px;  top: 520px; }

  /* Brand name block */
  .brand {
    position: absolute;
    display: flex;
    align-items: center;
    gap: 10px;
    font-weight: 600;
    color: var(--ink);
    letter-spacing: 0.01em;
    white-space: nowrap;
  }
  .brand__mark {
    width: 14px; height: 14px;
    background: var(--brand-green);
    flex: none;
  }

  /* Front */
  .card--front .brand { left: 28px; top: 142px; font-size: 20px; }
  .divider {
    position: absolute;
    left: 286px; top: 70px;
    width: 2px; height: 175px;
    background: var(--brand-green);
  }
  .contact { position: absolute; left: 306px; top: 82px; }
  .contact__name {
    color: var(--brand-green);
    font-weight: 600;
    font-size: 19px;
    letter-spacing: 0.04em;
    text-transform: uppercase;
    white-space: nowrap;
  }
  .contact__role {
    font-size: 10.5px;
    letter-spacing: 0.08em;
    text-transform: uppercase;
    margin-bottom: 14px;
  }
  .contact__list { list-style: none; }
  .contact__item {
    display: flex; align-items: center; gap: 8px;
    font-size: 11.5px; line-height: 22px;
    white-space: nowrap;
  }
  .contact__icon { width: 14px; height: 14px; flex: none; }

  /* Back */
  .services { position: absolute; left: 34px; top: 28px; }
  .services__title {
    color: var(--brand-green);
    font-weight: 600;
    font-size: 17px;
    letter-spacing: 0.03em;
    margin-bottom: 4px;
  }
  .services__list { list-style: none; }
  .services__item {
    font-size: 12.5px; line-height: 19.5px;
    display: flex; align-items: center; gap: 10px;
    white-space: nowrap;
  }
  .services__item::before {
    content: "✳";
    color: var(--brand-green);
    font-size: 11px;
  }
  .social {
    position: absolute; right: 36px; top: 150px;
    display: flex; gap: 8px;
  }
  .social__tile { width: 24px; height: 24px; background: var(--brand-green); }
  .card--back .brand { right: 36px; bottom: 42px; font-size: 22px; }
</style>
</head>
<body>

<section class="card card--front" aria-label="Card front">
  <div class="brand"><span class="brand__mark"></span>TMW Home Crafting</div>
  <div class="divider"></div>
  <div class="contact">
    <p class="contact__name">Liam Ashcroft</p>
    <p class="contact__role">General Manager</p>
    <ul class="contact__list">
      <li class="contact__item">
        <svg class="contact__icon" viewBox="0 0 14 14"><circle cx="7" cy="7" r="7" fill="#1f9a45"/><path d="M4.5 3.5h2l.6 2-1 .8a5 5 0 0 0 2.6 2.6l.8-1 2 .6v2a1 1 0 0 1-1 1A7 7 0 0 1 3.5 4.5a1 1 0 0 1 1-1z" fill="#000" transform="scale(.8) translate(1.8 1.8)"/></svg>
        0400 123 456
      </li>
      <li class="contact__item">
        <svg class="contact__icon" viewBox="0 0 14 14"><circle cx="7" cy="7" r="7" fill="#1f9a45"/><rect x="3.5" y="4.5" width="7" height="5" fill="none" stroke="#000" stroke-width="1"/><path d="M3.5 4.5 7 7.3l3.5-2.8" fill="none" stroke="#000" stroke-width="1"/></svg>
        info@tmwhomecrafting.com.au
      </li>
      <li class="contact__item">
        <svg class="contact__icon" viewBox="0 0 14 14"><circle cx="7" cy="7" r="7" fill="#1f9a45"/><circle cx="7" cy="7" r="3.6" fill="none" stroke="#000" stroke-width="1"/><path d="M3.4 7h7.2M7 3.4c-1.8 2-1.8 5.2 0 7.2M7 3.4c1.8 2 1.8 5.2 0 7.2" fill="none" stroke="#000" stroke-width=".8"/></svg>
        www.tmwhomecrafting.com.au
      </li>
      <li class="contact__item">
        <svg class="contact__icon" viewBox="0 0 14 14"><circle cx="7" cy="7" r="7" fill="#1f9a45"/><path d="M7 11s-3-3.2-3-5.3a3 3 0 0 1 6 0C10 7.8 7 11 7 11z" fill="#000"/><circle cx="7" cy="5.7" r="1.1" fill="#1f9a45"/></svg>
        Kingston, Tasmania, Australia
      </li>
    </ul>
  </div>
</section>

<section class="card card--back" aria-label="Card back">
  <div class="services">
    <h2 class="services__title">OUR SERVICES</h2>
    <ul class="services__list">
      <li class="services__item">Custom homes</li>
      <li class="services__item">Architectural homes</li>
      <li class="services__item">New builds</li>
      <li class="services__item">Renovations</li>
      <li class="services__item">Extensions</li>
      <li class="services__item">Alterations</li>
      <li class="services__item">Project management</li>
      <li class="services__item">Kitchens</li>
      <li class="services__item">Bathrooms</li>
      <li class="services__item">Shop fit outs</li>
      <li class="services__item">Decks and more</li>
    </ul>
  </div>
  <div class="social" aria-label="Social media">
    <span class="social__tile"></span>
    <span class="social__tile"></span>
  </div>
  <div class="brand"><span class="brand__mark"></span>TMW Home Crafting</div>
</section>

</body>
</html>
```